Business card for Crestline Bathrooms

Please design a business card for our bathroom renovation business. You can use my existing logo, but if you have an idea to modernize it, I would like to see it. Please see attached files first. I would like to use the blue and the orange theme. I like the concept of using the shower head in the logo. Please find following a design (or two) that I have been trying to create with my limited resources. That design was for a sign, but I was going to adopt it and use it as a business card as well. I like the concept of the water splash but I don’t think it “flows” nicely together with the logo. Another thought is that maybe creating the logo out of water splash could work and have a dramatic effect (like the water text and the butterfly picture attached with similar background instead of white). If the above doesn’t work I would like to see a modern simplified design. One of the attached files named as the unwanted business card has all the details that I want included in the business card. Please note that it is two sided.
Updates

I am very thankful for the designs that I have received, but they are very similar and only a couple of attempts to do something with the water splash as per my original brief. Modernizing the logo and having it made out of out of water splash with the orange as color accent could work and have a dramatic effect (like the water text and the butterfly picture attached with similar background instead of white). Please do not use the butterfly itself! This is just an example that images can be created out of water splash.

Contact Information for Business Card

all the details are on the unwonted business card file included

Colors
3176b5

Requirements
Nice to have
• Copied from the brief:
• ... maybe creating the logo out of water splash could work and have a dramatic effect (like the water text and the butterfly picture attached with similar background instead of white). Please do not use the butterfly itself!
Should not have
• I am getting designs with a butterfly. The butterfly picture was an example of creating something from a water splash. The butterfly itself has no association with anything other than the concept of creating a logo out of water splash. Sorry, I thought I was clear in the brief.

```html
<!DOCTYPE html>
<html lang="en">
<head>
<meta charset="utf-8">
<title>Crestline Bathrooms – Business Card</title>
<link rel="stylesheet" href="https://fonts.googleapis.com/css2?family=Roboto:wght@400&family=Delius&display=swap">
<style>
  :root {
    --page-bg: #e4e4e4;
    --card-navy: #1a3152;
    --splash-light: #c9d6e6;
    --splash-mid: #4f6f99;
    --accent-coral: #ea7461;
    --text-white: #ffffff;
    --badge-blue: #5b7cae;
  }
  * { box-sizing: border-box; margin: 0; padding: 0; }
  html, body { width: 1200px; height: 960px; overflow: hidden; }
  body { background: var(--page-bg); position: relative; font-family: "Roboto", sans-serif; }

  .card {
    position: absolute;
    width: 600px;
    height: 343px;
    background: var(--card-navy);
    overflow: hidden;
    box-shadow: 0 2px 5px rgba(0,0,0,0.35);
  }
  .card--back { left: 302px; top: 124px; }
  .card--front { left: 299px; top: 493px; }

  .splash { position: absolute; }
  .card--back .splash {
    left: 0; top: 0; width: 290px; height: 343px;
    background:
      radial-gradient(ellipse 150px 70px at 150px 320px, var(--splash-light) 0%, rgba(201,214,230,0.5) 40%, rgba(26,49,82,0) 100%),
      radial-gradient(ellipse 70px 170px at 40px 260px, rgba(201,214,230,0.55) 0%, rgba(79,111,153,0.3) 45%, rgba(26,49,82,0) 100%),
      radial-gradient(ellipse 110px 90px at 110px 40px, rgba(79,111,153,0.45) 0%, rgba(26,49,82,0) 100%);
  }
  .card--front .splash {
    right: 0; top: 0; width: 300px; height: 343px;
    background:
      radial-gradient(ellipse 150px 70px at 190px 300px, var(--splash-light) 0%, rgba(201,214,230,0.5) 40%, rgba(26,49,82,0) 100%),
      radial-gradient(ellipse 70px 170px at 250px 230px, rgba(201,214,230,0.55) 0%, rgba(79,111,153,0.3) 45%, rgba(26,49,82,0) 100%),
      radial-gradient(ellipse 120px 100px at 150px 40px, rgba(79,111,153,0.45) 0%, rgba(26,49,82,0) 100%);
  }

  .services {
    position: absolute; left: 212px; top: 106px;
    list-style: none; color: var(--text-white);
    font-size: 14px; line-height: 19px;
  }
  .services li { position: relative; padding-left: 14px; }
  .services li::before {
    content: ""; position: absolute; left: 0; top: 6px;
    width: 7px; height: 7px; border-radius: 50%; background: var(--accent-coral);
  }
  .memberships { position: absolute; left: 213px; top: 195px; display: flex; gap: 16px; align-items: center; }
  .badge { background: var(--badge-blue); }
  .badge--round { width: 30px; height: 30px; border-radius: 8px; }
  .badge--wide { width: 110px; height: 22px; border-radius: 3px; }

  .brand {
    position: absolute; left: 28px; top: 34px; width: 220px;
    display: flex; align-items: center; gap: 10px;
  }
  .brand-dot { flex: none; width: 18px; height: 18px; border-radius: 50%; background: var(--accent-coral); }
  .brand-name { color: var(--text-white); font-size: 34px; line-height: 40px; font-weight: 400; font-family: "Roboto", sans-serif; }

  .person-name {
    position: absolute; left: 27px; top: 174px;
    font-family: "Delius", cursive; font-size: 24px; color: var(--accent-coral);
  }
  .contacts { position: absolute; left: 28px; top: 216px; list-style: none; color: var(--text-white); font-size: 15px; }
  .contacts li { display: flex; align-items: center; height: 21px; }
  .contacts svg { width: 14px; height: 14px; margin-right: 9px; flex: none; fill: var(--accent-coral); }
</style>
</head>
<body>

<section class="card card--back" aria-label="Card back">
  <div class="splash" role="img" aria-label="Photograph of water splashing and dripping"></div>
  <ul class="services">
    <li>Complete Bathroom Renovations &amp; Remodelling</li>
    <li>Professional Service From Concept To Completion</li>
    <li>Highly Skilled &amp; Qualified Tradespeople</li>
    <li>All Work Guaranteed</li>
  </ul>
  <div class="memberships" aria-label="Industry memberships">
    <span class="badge badge--round"></span>
    <span class="badge badge--wide"></span>
  </div>
</section>

<section class="card card--front" aria-label="Card front">
  <div class="splash" role="img" aria-label="Photograph of water splashing and dripping"></div>
  <div class="brand">
    <span class="brand-dot"></span>
    <span class="brand-name">Crestline Bathrooms</span>
  </div>
  <p class="person-name">Daniel Rowhurst</p>
  <ul class="contacts">
    <li><svg viewBox="0 0 14 14"><path d="M4 0h6a1 1 0 0 1 1 1v12a1 1 0 0 1-1 1H4a1 1 0 0 1-1-1V1a1 1 0 0 1 1-1zm0 2v9h6V2z"/></svg>0400 318 742</li>
    <li><svg viewBox="0 0 14 14"><path d="M3 1l2 0 1.5 3.5-1.6 1.2a8 8 0 0 0 3.4 3.4l1.2-1.6L13 9v2a2 2 0 0 1-2 2C5.5 13 1 8.5 1 3a2 2 0 0 1 2-2z"/></svg>6100 4721</li>
    <li><svg viewBox="0 0 14 14"><path d="M7 1a6 6 0 1 0 3 11.2l-.6-1.1A4.7 4.7 0 1 1 11.7 7v.8a1 1 0 0 1-2 0V4h-1.2v.5A3 3 0 1 0 9 9.2a2.2 2.2 0 0 0 4-1.4V7A6 6 0 0 0 7 1zm0 4.2A1.8 1.8 0 1 1 7 8.8 1.8 1.8 0 0 1 7 5.2z"/></svg>daniel@crestlinebathrooms.com.au</li>
    <li><svg viewBox="0 0 14 14"><circle cx="7" cy="7" r="6"/><path d="M4 4h3v2H5zM8 8h2v3H8z" fill="#1a3152"/></svg>crestlinebathrooms.com.au</li>
    <li><svg viewBox="0 0 14 14"><path d="M1 3h12v8H1z"/><path d="M1 3l6 4.5L13 3" fill="none" stroke="#1a3152" stroke-width="1.2"/></svg>PO Box 18, Ridgeview 2600</li>
  </ul>
</section>

</body>
</html>
```